Animal Eye Clinic needs a Business card

We are a new veterinary ophthalmology practice (Ridgeline Pet Vision Care) and we need a business card designed. We only see animal eyes - we are not a regular veterinary clinic. We already have a logo. We are looking for a professional, good looking business card to hand out to our clients. We are looking for something simple but professional and contemporary. Our logo is likely the only picture/graphic that needs to be on the card.
Updates

Contact Information for Business Card

Delia Vossman, BSc, DVM, MSc, DipACVO
Veterinary Ophthalmologist

Phone: 250.418.3927
Email: ridgelinepetvisioncare@mailbox-example.net
Website: ridgelinepetvisioncare-example.net
Address: 1874 Thornbury Rd
Kelowna, BC, V1X 4M9

Colors

Designer to choose colors to be used in the design.

Requirements
Must have
• Our logo (attached)

```html
<!DOCTYPE html>
<html lang="en">
<head>
<meta charset="utf-8">
<title>Ridgeline Pet Vision Care — Business Card</title>
<link rel="stylesheet" href="https://fonts.googleapis.com/css2?family=Archivo:wght@700;800&family=Roboto+Condensed:wght@400&display=swap">
<style>
  :root {
    --backdrop: #2a2a2b;
    --card: #141414;
    --teal: #1a9fae;
    --text-grey: #9a9a9a;
    --rule: #1a9fae;
  }
  * { margin: 0; padding: 0; box-sizing: border-box; }
  html, body { width: 1200px; height: 900px; overflow: hidden; }
  body {
    background: var(--backdrop);
    position: relative;
    font-family: "Roboto Condensed", "Arial Narrow", sans-serif;
  }
  .card {
    position: absolute;
    left: 310px;
    width: 580px;
    height: 331px;
    background: var(--card);
    box-shadow: 0 8px 24px rgba(0,0,0,0.45);
  }
  .card--front { top: 60px; }
  .card--back { top: 470px; }

  /* Front */
  .front-brand {
    position: absolute;
    inset: 0;
    display: flex;
    align-items: center;
    justify-content: center;
    gap: 18px;
  }
  .front-brand__dot {
    width: 46px; height: 46px;
    border-radius: 50%;
    background: var(--teal);
  }
  .front-brand__name {
    font-family: "Archivo", sans-serif;
    font-weight: 800;
    font-size: 30px;
    letter-spacing: 0.5px;
    color: var(--teal);
    text-transform: uppercase;
    line-height: 1.05;
  }

  /* Back */
  .brand {
    position: absolute;
    top: 42px;
    left: 0; right: 0;
    display: flex;
    justify-content: center;
    align-items: center;
    gap: 10px;
  }
  .brand__dot {
    width: 22px; height: 22px;
    border-radius: 50%;
    background: var(--teal);
  }
  .brand__name {
    font-family: "Archivo", sans-serif;
    font-weight: 800;
    font-size: 19px;
    color: var(--teal);
    text-transform: uppercase;
  }
  .person {
    position: absolute;
    top: 142px;
    right: 312px;
    text-align: right;
  }
  .person__name {
    font-family: "Archivo", sans-serif;
    font-weight: 800;
    font-size: 27px;
    color: var(--teal);
    text-transform: uppercase;
    line-height: 1;
  }
  .person__credentials {
    font-family: "Archivo", sans-serif;
    font-weight: 700;
    font-size: 15px;
    color: var(--teal);
    margin-top: 4px;
  }
  .person__title {
    font-size: 17px;
    color: var(--text-grey);
    margin-top: 2px;
  }
  .divider {
    position: absolute;
    left: 284px;
    top: 138px;
    width: 2px;
    height: 96px;
    background: var(--rule);
  }
  .contacts {
    position: absolute;
    left: 302px;
    top: 150px;
    list-style: none;
  }
  .contacts__item {
    display: flex;
    align-items: center;
    gap: 9px;
    font-size: 15px;
    color: var(--text-grey);
    height: 26px;
  }
  .contacts__icon { width: 17px; height: 17px; flex: none; }
  .address {
    position: absolute;
    left: 0; right: 0;
    bottom: 36px;
    text-align: center;
    font-size: 17px;
    color: var(--text-grey);
  }
</style>
</head>
<body>

<section class="card card--front" aria-label="Card front">
  <div class="front-brand">
    <span class="front-brand__dot"></span>
    <span class="front-brand__name">Ridgeline Pet<br>Vision Care</span>
  </div>
</section>

<section class="card card--back" aria-label="Card back">
  <div class="brand">
    <span class="brand__dot"></span>
    <span class="brand__name">Ridgeline Pet Vision Care</span>
  </div>

  <div class="person">
    <p class="person__name">Delia Vossman</p>
    <p class="person__credentials">BSc, DVM, MSc, DipACVO</p>
    <p class="person__title">Veterinary Ophthalmologist</p>
  </div>

  <div class="divider"></div>

  <ul class="contacts">
    <li class="contacts__item">
      <svg class="contacts__icon" viewBox="0 0 20 20" fill="none" stroke="#1a9fae" stroke-width="1.6">
        <circle cx="10" cy="10" r="8"/>
        <path d="M7 6.2c.6-.6 1.2-.4 1.5.2l.6 1.2c.2.5 0 .9-.4 1.2-.3.2-.3.6 0 1 .5.7 1 1.2 1.6 1.6.4.3.8.3 1-.1.3-.4.8-.5 1.2-.3l1.1.6c.6.3.7 1 .2 1.5-1 1-2.5.9-4-.3-1.3-1-2.3-2.2-3-3.6-.6-1.3-.6-2.4.2-3z" fill="#1a9fae" stroke="none"/>
      </svg>
      250.418.3927
    </li>
    <li class="contacts__item">
      <svg class="contacts__icon" viewBox="0 0 20 20" fill="none" stroke="#1a9fae" stroke-width="1.6">
        <rect x="2" y="4.5" width="16" height="11" rx="1"/>
        <path d="M2.5 5l7.5 6 7.5-6"/>
      </svg>
      ridgelinepetvisioncare@mailbox-example.net
    </li>
    <li class="contacts__item">
      <svg class="contacts__icon" viewBox="0 0 20 20" fill="none" stroke="#1a9fae" stroke-width="1.6">
        <circle cx="10" cy="10" r="8"/>
        <ellipse cx="10" cy="10" rx="3.5" ry="8"/>
        <path d="M2 10h16M3.5 6h13M3.5 14h13"/>
      </svg>
      www.ridgelinepetvisioncare-example.net
    </li>
  </ul>

  <p class="address">1874 Thornbury Rd, Kelowna, BC, V1X 4M9</p>
</section>

</body>
</html>
```